Create a Big Data Website that is professional but has a creative flare to it.

I am after a modern business design for a company in the Big Data space however it still needs to have a wow value and something stand out from other corporate websites.
My competitors websites are to give you and idea of content:
www.tarnvilla.com
www.pluvoria.com
www.meridu4.com.au
www.quornaby.com
I have uploaded my company Logo so you can use that to make sure it matches your theme.

Target Market(s)

Banks, Insurance Companies, Government, Gas and Energy Companies and Food Manufacturing.

Industry/Entity Type

Consulting

Coding

Number of Pages Required

5+ page

Colors

Designer to choose colors to be used in the design.

Requirements
Must have
• Images, Diagrams around Big Data. Usage of information or graphs from sources like Velsham are fine to use.
Nice to have
• Interactive design use mouse overs, change in text, highlighting information for clear focus.
Should not have
• Cluttered Pages of Informaiton

```html
<!DOCTYPE html>
<html lang="en">
<head>
<meta charset="utf-8">
<title>Veridane Consulting – Big Data</title>
<link rel="stylesheet" href="https://fonts.googleapis.com/css2?family=Open+Sans:wght@400;600&family=Roboto+Condensed:wght@700&family=Roboto:wght@400;500;700&display=swap">
<style>
:root{
  --navy:#1d3f7d;
  --blue:#1a7fd0;
  --sky:#2b9ad8;
  --sky-light:#6cc2ec;
  --band:#22549a;
  --ink:#222;
  --muted:#666;
  --line:#e3e6ea;
  --footer:#151515;
  --white:#fff;
}
*{box-sizing:border-box;margin:0;padding:0}
html,body{width:1200px;height:3321px;overflow:hidden;background:var(--white)}
body{font-family:"Open Sans",Arial,sans-serif;color:var(--ink);position:relative}
.page{position:relative;width:1200px;height:3321px;overflow:hidden}
.abs{position:absolute}

/* header */
.site-header{top:0;left:0;width:1200px;height:100px;background:var(--white);z-index:3}
.brand{left:98px;top:24px;display:flex;align-items:center;gap:12px}
.brand-mark{width:40px;height:40px;background:var(--blue)}
.brand-name{font-family:"Roboto",sans-serif;font-weight:700;font-size:34px;color:var(--navy);line-height:1}
.brand-sub{font-family:"Roboto",sans-serif;font-weight:700;font-size:34px;color:var(--navy)}
.main-nav{right:96px;top:38px;display:flex;gap:30px;font-family:"Roboto",sans-serif;font-size:14px;font-weight:500;color:#333;text-transform:uppercase}
.main-nav .active{color:var(--blue)}
.main-nav .lang{border-left:1px solid #ccc;padding-left:10px}

/* hero */
.hero{top:100px;left:0;width:1200px;height:600px}
.hero-photo{position:absolute;inset:0;background:linear-gradient(100deg,#4d5a68 0%,#2a3341 30%,#151c28 60%,#222c3b 100%)}
.hero-cut{position:absolute;left:0;top:500px;width:1200px;height:100px}
.hero-copy{position:absolute;left:775px;top:170px;width:360px;color:var(--white)}
.hero-title{font-family:"Roboto Condensed",sans-serif;font-weight:700;font-size:47px;line-height:50px;text-transform:uppercase}
.hero-text{font-size:13px;line-height:21px;margin-top:14px}
.btn-pill{display:inline-flex;align-items:center;gap:8px;border-radius:20px;padding:0 18px;height:36px;font-family:"Roboto",sans-serif;font-size:13px;font-weight:500;text-transform:uppercase}
.hero .btn-pill{background:var(--blue);color:var(--white);margin-top:24px;height:34px}
.slider-dots{position:absolute;left:572px;top:524px;display:flex;gap:6px}
.slider-dots i{width:12px;height:12px;border-radius:50%;border:2px solid #ccc;background:transparent}
.slider-dots i.on{background:var(--white);border-color:var(--white)}

/* welcome */
.section-title{font-family:"Roboto",sans-serif;font-size:34px;font-weight:400;text-align:center;color:#222;text-transform:uppercase;letter-spacing:.5px}
.section-title strong{color:var(--navy);font-weight:700}
.title-rule{width:52px;height:3px;background:var(--navy);margin:20px auto 0}
.welcome{top:762px;left:0;width:1200px}
.welcome-text{width:970px;margin:28px auto 0;font-size:11.5px;line-height:22px;text-align:center;color:#555}
.features{top:978px;left:0;width:1200px;display:flex;justify-content:center;gap:0}
.feature{width:265px;text-align:center}
.feature svg{display:block;margin:0 auto}
.feature h3{font-family:"Roboto",sans-serif;font-weight:400;font-size:19px;color:#333;margin-top:24px}
.feature p{font-size:11.5px;line-height:20px;color:#666;margin:12px auto 0;width:220px}
.feature .chev{margin-top:14px}

/* analytics band */
.analytics-band{top:1311px;left:0;width:1200px;height:488px;background:linear-gradient(180deg,#2390d2 0%,#39a8e2 60%,#8fd0ef 100%)}
.analytics-art{position:absolute;left:30px;top:120px;width:590px;height:360px;background:radial-gradient(ellipse at 55% 45%,#dff2fb 0%,#9fd3ee 45%,rgba(60,160,220,0) 75%)}
.analytics-copy{position:absolute;left:660px;top:122px;width:480px;color:var(--white)}
.analytics-copy h2{font-family:"Roboto",sans-serif;font-weight:700;font-size:38px;text-transform:uppercase}
.analytics-copy p{font-size:11.5px;line-height:21px;margin-top:12px}
.analytics-copy .btn-pill{background:var(--navy);color:var(--white);margin-top:18px}

/* solutions */
.solutions{top:1872px;left:0;width:1200px}
.cards{top:1984px;left:97px;width:1001px;display:flex;justify-content:space-between}
.card{width:310px}
.card-media{width:310px;height:195px}
.media-enrich{background:linear-gradient(135deg,#c99a6a,#e8d6c0 55%,#8b6a4a)}
.media-visual{background:linear-gradient(135deg,#0d1624,#2a3d58 60%,#101a28)}
.media-predict{background:linear-gradient(135deg,#0d3a66,#3a8fc4 55%,#0b2c50)}
.card h3{font-family:"Roboto",sans-serif;font-weight:400;font-size:19px;color:#222;margin-top:22px}
.card p{font-size:11.5px;line-height:20px;color:#666;margin-top:10px;width:300px}
.btn-outline{display:inline-flex;align-items:center;gap:5px;border:1px solid var(--navy);color:var(--navy);font-family:"Roboto",sans-serif;font-size:11px;font-weight:500;padding:0 8px;height:28px;margin-top:20px;text-transform:uppercase}

/* testimonial */
.testimonial{top:2418px;left:0;width:1200px;height:405px;background:linear-gradient(160deg,#1f5aa3 0%,#234f92 50%,#1c467f 100%);color:var(--white);text-align:center}
.testimonial-name{padding-top:100px;font-family:"Roboto",sans-serif;font-weight:700;font-size:30px}
.quote{width:980px;margin:34px auto 0;font-size:11.5px;line-height:21px;position:relative}
.quote::before{content:"\201C";position:absolute;left:-6px;top:-10px;font-size:34px;font-family:Georgia,serif}
.quote-author{margin-top:14px;font-style:italic;font-size:16px}
.quote-author small{font-size:12px}
.quote-dots{display:flex;justify-content:center;gap:6px;margin-top:22px}
.quote-dots i{width:26px;height:2px;background:rgba(255,255,255,.45)}
.quote-dots i.on{background:var(--white)}

/* partners */
.partners{top:2823px;left:0;width:1200px;height:128px;display:flex;justify-content:center;align-items:center;gap:52px}
.partner-badge{width:110px;height:36px;background:#cfd2d6;border-radius:3px}

/* footer */
.site-footer{top:2951px;left:0;width:1200px;height:370px;background:var(--footer);color:#ddd}
.footer-brand{position:absolute;left:80px;top:70px;width:200px;text-align:center}
.footer-brand .brand-name{color:var(--white);font-size:32px}
.socials{display:flex;justify-content:center;gap:8px;margin-top:20px}
.socials i{width:20px;height:20px;border-radius:50%;background:var(--white)}
.footer-col{position:absolute;top:60px}
.footer-col h4{font-family:"Roboto",sans-serif;font-weight:500;font-size:17px;color:var(--white);text-transform:uppercase;margin-bottom:22px}
.contact-list{list-style:none;font-size:12px;line-height:20px}
.contact-list li{display:flex;gap:18px;margin-bottom:16px}
.contact-list svg{flex:none;margin-top:2px}
.signup p{font-size:11.5px;line-height:20px;width:290px}
.signup .field{width:285px;height:40px;background:var(--white);color:#444;font-size:11px;padding:12px 10px;margin-top:16px}
.signup .btn-sub{display:inline-block;margin-top:18px;background:var(--blue);color:var(--white);font-size:11px;padding:11px 14px;text-transform:uppercase}
.links{list-style:none;font-size:12px;line-height:24px}
.copyright{position:absolute;top:327px;left:0;width:1200px;text-align:center;font-size:12px;color:#ccc}
</style>
</head>
<body>
<div class="page">

  <header class="site-header abs">
    <div class="brand abs">
      <span class="brand-mark"></span>
      <span class="brand-name">Veridane Consulting</span>
    </div>
    <nav class="main-nav abs">
      <span class="active">Home</span><span>About Us</span><span>Our Services</span><span>Partners</span><span>Contact Us</span><span class="lang">EN ▾</span>
    </nav>
  </header>

  <section class="hero abs">
    <div class="hero-photo" role="img" aria-label="Consultant working on a laptop in a server room"></div>
    <svg class="hero-cut" width="1200" height="100" viewBox="0 0 1200 100">
      <polygon points="0,30 600,86 1200,50 1200,100 0,100" fill="#fff"/>
      <polyline points="0,30 600,86 1200,50" fill="none" stroke="#1a7fd0" stroke-width="2"/>
    </svg>
    <div class="hero-copy">
      <h1 class="hero-title">Create Value<br>From Data</h1>
      <p class="hero-text">Sed ut perspiciatis unde omnis iste natus error sit voluptatem accusantium doloremque laudantium, totam rem aperiam, eaque ipsa quae</p>
      <span class="btn-pill">Read More
        <svg width="12" height="12" viewBox="0 0 12 12"><circle cx="6" cy="6" r="6" fill="#fff"/><path d="M5 3l3 3-3 3" fill="none" stroke="#1a7fd0" stroke-width="1.6"/></svg>
      </span>
    </div>
    <div class="slider-dots"><i class="on"></i><i></i><i></i></div>
  </section>

  <section class="welcome abs">
    <h2 class="section-title">Welcome to <strong>Veridane Consulting</strong></h2>
    <div class="title-rule"></div>
    <p class="welcome-text">Lorem ipsum dolor sit amet, consectetur adipiscing elit, sed do eiusmod tempor incididunt ut labore et dolore magna aliqua. Ut enim ad minim veniam, quis nostrud exercitation ullamco laboris nisi ut aliquip ex ea commodo consequat. Duis aute irure dolor in reprehenderit in voluptate velit esse cillum dolore eu fugiat nulla pariatur. Excepteur sint occaecat cupidatat non proident, sunt in culpa qui officia deserunt mollit anim id est laborum</p>
  </section>

  <div class="features abs">
    <div class="feature">
      <svg width="120" height="104" viewBox="0 0 120 104"><polygon points="30,2 90,2 118,52 90,102 30,102 2,52" fill="none" stroke="#1a7fd0" stroke-width="4"/><polygon points="35,11 85,11 108,52 85,93 35,93 12,52" fill="#1a7fd0"/><path d="M48 32h18l8 8v32H48z" fill="#fff"/><path d="M54 50h14M54 57h14M54 64h10" stroke="#1a7fd0" stroke-width="3"/></svg>
      <h3>Strategic Execution</h3>
      <p>Nemo enim ipsam voluptatem quia volut sit aspernatur aut odit aut fugit, sed quia consequuntur magni dolores</p>
      <svg class="chev" width="14" height="12" viewBox="0 0 14 12"><path d="M2 1l5 4 5-4M2 6l5 4 5-4" fill="none" stroke="#1a7fd0" stroke-width="1.6"/></svg>
    </div>
    <div class="feature">
      <svg width="120" height="104" viewBox="0 0 120 104"><polygon points="30,2 90,2 118,52 90,102 30,102 2,52" fill="none" stroke="#1d3f7d" stroke-width="4"/><polygon points="35,11 85,11 108,52 85,93 35,93 12,52" fill="#1d3f7d"/><rect x="42" y="36" width="36" height="26" fill="none" stroke="#fff" stroke-width="3"/><path d="M47 56l9-9 6 5 11-11" fill="none" stroke="#fff" stroke-width="2.5"/><path d="M52 68h16" stroke="#fff" stroke-width="3"/></svg>
      <h3>Expert Code</h3>
      <p>Nemo enim ipsam voluptatem quia volut sit aspernatur aut odit aut fugit, sed quia consequuntur magni dolores</p>
      <svg class="chev" width="14" height="12" viewBox="0 0 14 12"><path d="M2 1l5 4 5-4M2 6l5 4 5-4" fill="none" stroke="#1d3f7d" stroke-width="1.6"/></svg>
    </div>
    <div class="feature">
      <svg width="120" height="104" viewBox="0 0 120 104"><polygon points="30,2 90,2 118,52 90,102 30,102 2,52" fill="none" stroke="#1a7fd0" stroke-width="4"/><polygon points="35,11 85,11 108,52 85,93 35,93 12,52" fill="#1a7fd0"/><circle cx="55" cy="56" r="11" fill="none" stroke="#fff" stroke-width="6" stroke-dasharray="5 3"/><circle cx="55" cy="56" r="4" fill="#fff"/><circle cx="72" cy="41" r="7" fill="none" stroke="#fff" stroke-width="4" stroke-dasharray="3 2"/></svg>
      <h3>Flexible Solutions</h3>
      <p>Nemo enim ipsam voluptatem quia volut sit aspernatur aut odit aut fugit, sed quia consequuntur magni dolores</p>
      <svg class="chev" width="14" height="12" viewBox="0 0 14 12"><path d="M2 1l5 4 5-4M2 6l5 4 5-4" fill="none" stroke="#1a7fd0" stroke-width="1.6"/></svg>
    </div>
    <div class="feature">
      <svg width="120" height="104" viewBox="0 0 120 104"><polygon points="30,2 90,2 118,52 90,102 30,102 2,52" fill="none" stroke="#1d3f7d" stroke-width="4"/><polygon points="35,11 85,11 108,52 85,93 35,93 12,52" fill="#1d3f7d"/><circle cx="60" cy="52" r="18" fill="none" stroke="#fff" stroke-width="4"/><circle cx="60" cy="52" r="8" fill="none" stroke="#fff" stroke-width="4"/><path d="M47 39l7 7M73 39l-7 7M47 65l7-7M73 65l-7-7" stroke="#fff" stroke-width="4"/></svg>
      <h3>Quality Support</h3>
      <p>Nemo enim ipsam voluptatem quia volut sit aspernatur aut odit aut fugit, sed quia consequuntur magni dolores</p>
      <svg class="chev" width="14" height="12" viewBox="0 0 14 12"><path d="M2 1l5 4 5-4M2 6l5 4 5-4" fill="none" stroke="#1d3f7d" stroke-width="1.6"/></svg>
    </div>
  </div>

  <section class="analytics-band abs">
    <div class="analytics-art" role="img" aria-label="Illustration of devices showing charts under a magnifying glass among clouds"></div>
    <div class="analytics-copy">
      <h2>Big Data Analytics</h2>
      <p>Sed ut perspiciatis unde omnis iste natus error sit voluptatem accusantium doloremque laudantium, totam rem aperiam, eaque ipsa quae ab illo inventore veritatis et quasi architecto beatae vitae dicta sunt explicabo. Nemo enim ipsam voluptatem quia voluptas sit aspernatur aut odit aut fugit, sed quia consequuntur</p>
      <span class="btn-pill">Read More</span>
    </div>
  </section>

  <section class="solutions abs">
    <h2 class="section-title"><strong style="color:#222">Big Data Analytics Solutions</strong></h2>
    <div class="title-rule"></div>
  </section>

  <div class="cards abs">
    <article class="card">
      <div class="card-media media-enrich" role="img" aria-label="Team reviewing data reports on a desk"></div>
      <h3>Data Enrichment</h3>
      <p>Sed ut perspiciatis unde omnis iste natus error sit voluptatem accusantium doloremque laudantium, totam rem aperiam, eaque ipsa quae</p>
      <span class="btn-outline">Read More <svg width="9" height="9" viewBox="0 0 10 10"><circle cx="5" cy="5" r="5" fill="#1d3f7d"/><path d="M4 3l2 2-2 2" fill="none" stroke="#fff" stroke-width="1.3"/></svg></span>
    </article>
    <article class="card">
      <div class="card-media media-visual" role="img" aria-label="Hands presenting stacked data blocks on a dark background"></div>
      <h3>Data Visualisation</h3>
      <p>Sed ut perspiciatis unde omnis iste natus error sit voluptatem accusantium doloremque laudantium, totam rem aperiam, eaque ipsa quae</p>
      <span class="btn-outline">Read More <svg width="9" height="9" viewBox="0 0 10 10"><circle cx="5" cy="5" r="5" fill="#1d3f7d"/><path d="M4 3l2 2-2 2" fill="none" stroke="#fff" stroke-width="1.3"/></svg></span>
    </article>
    <article class="card">
      <div class="card-media media-predict" role="img" aria-label="Businessman facing a glowing digital data interface"></div>
      <h3>Predictive Analytics</h3>
      <p>Sed ut perspiciatis unde omnis iste natus error sit voluptatem accusantium doloremque laudantium, totam rem aperiam, eaque ipsa quae</p>
      <span class="btn-outline">Read More <svg width="9" height="9" viewBox="0 0 10 10"><circle cx="5" cy="5" r="5" fill="#1d3f7d"/><path d="M4 3l2 2-2 2" fill="none" stroke="#fff" stroke-width="1.3"/></svg></span>
    </article>
  </div>

  <section class="testimonial abs">
    <div class="testimonial-name">Veridane</div>
    <p class="quote">Lorem ipsum dolor sit amet, consectetur adipiscing elit, sed do eiusmod tempor incididunt ut labore et dolore magna aliqua. Ut enim ad minim veniam, quis nostrud exercitation ullamco laboris nisi ut aliquip ex ea commodo consequat. Duis aute irure dolor in reprehenderit in voluptate velit esse cillum dolore eu fugiat nulla Sed ut perspiciatis unde omnis iste natus error sit voluptatem accusantium doloremque laudantium, totam rem aperiam, eaque ipsa quae ab illo inventore veritatis et quasi architecto beatae vitae</p>
    <p class="quote-author">John Doe <small>– Veridane Consulting</small></p>
    <div class="quote-dots"><i class="on"></i><i></i><i></i></div>
  </section>

  <section class="partners abs" aria-label="Partners">
    <span class="partner-badge"></span><span class="partner-badge"></span><span class="partner-badge"></span><span class="partner-badge"></span><span class="partner-badge"></span><span class="partner-badge"></span>
  </section>

  <footer class="site-footer abs">
    <div class="footer-brand">
      <div class="brand-name">Veridane</div>
      <div class="socials"><i></i><i></i><i></i><i></i><i></i></div>
    </div>
    <div class="footer-col" style="left:341px">
      <h4>Contact Us</h4>
      <ul class="contact-list">
        <li><svg width="14" height="18" viewBox="0 0 14 18"><path d="M7 17S1 10 1 6.5a6 6 0 0112 0C13 10 7 17 7 17z" fill="none" stroke="#fff" stroke-width="1.5"/><circle cx="7" cy="6.5" r="2" fill="#fff"/></svg><span>Veridane Consulting<br>412 Larchmont Way, Alberta</span></li>
        <li><svg width="14" height="16" viewBox="0 0 14 16"><path d="M3 1l3 3-2 2c1 2 3 4 5 5l2-2 3 3-2 3C6 14 0 8 1 3z" fill="none" stroke="#fff" stroke-width="1.4"/></svg><span>(403) 555-0142<br>+44 (0)20 7946 0321</span></li>
        <li><svg width="16" height="12" viewBox="0 0 16 12"><rect x="1" y="1" width="14" height="10" fill="none" stroke="#fff" stroke-width="1.4"/><path d="M1 1l7 6 7-6" fill="none" stroke="#fff" stroke-width="1.4"/></svg><span>info@veridaneconsulting.com</span></li>
      </ul>
    </div>
    <div class="footer-col signup" style="left:644px">
      <h4>Sign Up to Receive Email</h4>
      <p>Excepteur sint occaecat cupidatat non proident, sunt in culpa qui Nemo enim ipsam voluptatem</p>
      <div class="field">Enter Name</div>
      <span class="btn-sub">Subscribe</span>
    </div>
    <div class="footer-col" style="left:994px">
      <h4>Quick Links</h4>
      <ul class="links"><li>Home</li><li>Partners</li><li>Services</li><li>Downloads</li><li>Events</li><li>Contact</li></ul>
    </div>
    <p class="copyright">Copyright © Veridane Consulting 2017. All rights reserved.</p>
  </footer>

</div>
</body>
</html>
```